Website Needs Designing / Populating

We are a Business Consultancy in London. We are Headhunters and Recruitment. I have bought the Domain, and Wordpress Site, installed a template from Brindle Orchard. I have tried to do it myself but do not have the time to complete or do it as I want / need.
I have some 'stock' pics and a logo - see uploaded logo files.
I want an easy to use Website - tells clients and viewers what we are about.
We are a recruitment / Headhunting Consultancy so some visitors may want to apply for positions through loading their CV / Details through the site.
We want to be about friendly but expertise. Honest and trustworthy with a heavy emphasis on Consultancy!

Target Market(s)

IT and Finance Job Seekers. Our clients are in the Marketing Communications sectors so needs to be appealing to that market

Industry/Entity Type

Business Consultant

Number of Pages Required

3 page

Requirements
Must have
• Our Logo as a central theme - see uploaded files
Nice to have
• Simple. Easy to use, inviting

```html
<!DOCTYPE html>
<html lang="en">
<head>
<meta charset="utf-8">
<title>caldermoor Recruitment</title>
<link rel="stylesheet" href="https://fonts.googleapis.com/css2?family=Raleway:wght@400;500;600;700&display=swap">
<style>
:root{
  --blue:#0f9be0;
  --ink:#222;
  --text:#555;
  --muted:#8a8a8a;
  --grey-btn:#5f5f5f;
  --line:#e3e3e3;
  --footer:#2b2b2b;
  --yellow:#f4c21c;
  --white:#fff;
}
*{box-sizing:border-box;margin:0;padding:0}
html,body{width:1200px;height:2459px;overflow:hidden}
body{position:relative;font-family:'Raleway',Arial,sans-serif;color:var(--text);background:var(--white)}
.abs{position:absolute}
.btn{position:absolute;display:flex;align-items:center;justify-content:center;color:var(--white);font-size:14px;font-weight:500;border-radius:2px}
.btn--blue{background:var(--blue)}
.btn--grey{background:var(--grey-btn)}

/* top bar */
.topbar{left:0;top:0;width:1200px;height:43px;background:var(--blue);color:var(--white);font-size:14px}
.topbar__contact{left:98px;top:12px}
.topbar__social{top:13px;width:14px;height:14px;border-radius:50%;background:rgba(255,255,255,.85)}

/* hero */
.hero{left:0;top:43px;width:1200px;height:586px;background:linear-gradient(100deg,#f1f3f5 0%,#e6eaee 40%,#a9b6c4 62%,#4d6078 80%,#2c3f5c 100%)}
.header{left:0;top:43px;width:1200px;height:100px;background:rgba(255,255,255,.92);border-bottom:1px solid #ddd}
.logo{left:98px;top:64px;display:flex;align-items:center;gap:10px;font-size:40px;font-weight:600;color:#4a4a4a;letter-spacing:-1px}
.logo__mark{width:12px;height:12px;background:var(--blue)}
.nav{top:90px;font-size:16px;color:#333}
.nav--active{border-bottom:2px solid #333;padding-bottom:10px}
.hero__title{left:98px;top:245px;font-size:38px;font-weight:700;color:var(--ink)}
.hero__lead{left:98px;top:316px;font-size:18px;line-height:29px;color:#333}
.hero__arrow{top:388px}
.cta-band{left:0;top:629px;width:1200px;height:72px;background:var(--blue)}
.cta-band__text{left:115px;top:652px;font-size:20px;font-weight:500;color:var(--white)}

/* section headings */
.section-title{left:0;width:1200px;text-align:center;font-size:26px;font-weight:500;color:var(--ink)}
.section-title span{color:var(--blue)}
.section-lead{left:160px;width:880px;text-align:center;font-size:13px;line-height:20px;color:var(--muted)}

/* service cards */
.service{top:893px;width:290px;height:333px;background:var(--white);border:1px solid var(--line);box-shadow:0 10px 10px -8px rgba(0,0,0,.25)}
.service__icon{position:absolute;left:88px;top:22px;width:114px;height:114px;border-radius:50%;border:2px solid #bbb;padding:4px}
.service__icon div{width:100%;height:100%;border-radius:50%;background:#6b6b6b;display:flex;align-items:center;justify-content:center}
.service--active .service__icon{border-color:var(--blue)}
.service--active .service__icon div{background:var(--blue)}
.service__title{position:absolute;left:0;top:157px;width:100%;text-align:center;font-size:17px;font-weight:500;color:var(--ink)}
.service__text{position:absolute;left:25px;top:190px;width:240px;text-align:center;font-size:13px;line-height:20px;color:#444}
.service .btn{left:91px;top:272px;width:108px;height:36px}

/* job search band */
.search-band{left:0;top:1293px;width:1200px;height:277px;background:linear-gradient(90deg,#e9edf1 0%,#8797ad 25%,#4c5f7c 55%,#2f4261 75%,#3b4d6a 100%)}
.search-band__tick{left:100px;top:1360px}
.search-band__title{left:157px;top:1358px;font-size:31px;font-weight:700;line-height:44px}
.search-band__title .hl{color:var(--yellow)}
.search-band__title .wh{color:var(--white)}
.search-input{left:159px;top:1475px;width:298px;height:48px;background:#eef0f2;border:1px solid #ccc;font-size:13px;color:#666;padding:15px 12px}

/* blog cards */
.post{top:1739px;width:299px;height:343px;border:1px solid var(--line);background:var(--white)}
.post__image{position:absolute;left:6px;top:6px;width:285px;height:156px}
.post__title{position:absolute;left:11px;top:179px;font-size:15px;font-weight:600;color:var(--ink)}
.post__text{position:absolute;left:11px;top:210px;width:278px;font-size:13px;line-height:20px;color:#444}
.post .btn{left:12px;top:287px;width:101px;height:37px}

/* footer */
.footer{left:0;top:2134px;width:1200px;height:264px;background:var(--footer)}
.footer__logo{left:98px;top:2180px;display:flex;align-items:center;gap:9px;font-size:34px;font-weight:600;color:var(--white);letter-spacing:-1px}
.footer__logo i{width:10px;height:10px;background:var(--blue)}
.footer__about{left:98px;top:2258px;width:220px;font-size:13px;line-height:20px;color:#ddd}
.footer__head{top:2181px;font-size:15px;font-weight:500;color:var(--white)}
.footer__links{left:370px;top:2217px;list-style:none;font-size:13px;line-height:24px;color:#ddd}
.footer__contact{left:554px;top:2215px;font-size:13px;line-height:29px;color:#ddd}
.footer__contact li{list-style:none;display:flex;gap:14px;align-items:flex-start}
.footer__contact svg{margin-top:8px;flex:none}
.footer__news{left:847px;top:2210px;width:260px;font-size:12px;line-height:20px;color:#ddd}
.news-input{left:847px;top:2270px;width:253px;height:33px;border:1px solid #888;font-size:12px;color:#eee;padding:9px}
.news-btn{left:847px;top:2318px;width:253px;height:32px;font-size:13px}
.bottombar{left:0;top:2398px;width:1200px;height:61px;background:var(--blue)}
.bottombar__copy{left:102px;top:2420px;font-size:13px;color:var(--white)}
.bottombar__social{top:2411px;width:31px;height:31px;border:2px solid var(--white);border-radius:50%}
</style>
</head>
<body>

<!-- top bar -->
<div class="abs topbar">
  <div class="abs topbar__contact">+33 100 20 30 40 &nbsp;&nbsp;|&nbsp;&nbsp; hello@caldermoor.example</div>
  <span class="abs topbar__social" style="left:957px"></span>
  <span class="abs topbar__social" style="left:999px"></span>
  <span class="abs topbar__social" style="left:1043px"></span>
  <span class="abs topbar__social" style="left:1088px"></span>
</div>

<!-- hero -->
<div class="abs hero" role="img" aria-label="Photo of two businessmen in suits reviewing a tablet together"></div>
<div class="abs header"></div>
<div class="abs logo"><span>caldermoor</span><i class="logo__mark"></i></div>
<nav>
  <span class="abs nav nav--active" style="left:542px">Home</span>
  <span class="abs nav" style="left:629px">About Us</span>
  <span class="abs nav" style="left:743px">Services</span>
  <span class="abs nav" style="left:852px">News</span>
  <span class="abs nav" style="left:941px">Blog</span>
  <span class="abs nav" style="left:1022px">Contact Us</span>
</nav>
<h1 class="abs hero__title">headhunters and recruitment</h1>
<p class="abs hero__lead">We are a Business Consultancy in London.<br>We are Headhunters and Recruitment</p>
<div class="btn btn--blue" style="left:98px;top:400px;width:126px;height:44px;font-size:15px">Read More</div>
<svg class="abs hero__arrow" style="left:20px" width="26" height="50" viewBox="0 0 26 50"><path d="M24 2 L3 25 L24 48" fill="none" stroke="#888" stroke-width="2"/></svg>
<svg class="abs hero__arrow" style="left:1156px" width="26" height="50" viewBox="0 0 26 50"><path d="M2 2 L23 25 L2 48" fill="none" stroke="#223" stroke-width="2"/></svg>

<div class="abs cta-band"></div>
<div class="abs cta-band__text">Looking for a First-Class Business Consultant?</div>
<div class="btn btn--grey" style="left:890px;top:644px;width:125px;height:41px;font-size:15px">Get a Quote</div>

<!-- services -->
<h2 class="abs section-title" style="top:759px">Our <span>Recruitment Services</span></h2>
<p class="abs section-lead" style="top:808px">A unique destination for everything that practitioners need to execute best practice change management, transformation and project methodologies. The Learning Hub offering will be positioned as a place of learning.</p>

<div class="abs service" style="left:98px">
  <div class="service__icon"><div>
    <svg width="40" height="40" viewBox="0 0 40 40" fill="none" stroke="#fff" stroke-width="2"><rect x="6" y="10" width="18" height="24"/><rect x="11" y="6" width="18" height="24" fill="#6b6b6b"/><rect x="16" y="2" width="18" height="24" fill="#6b6b6b"/><path d="M20 9h10M20 14h10M20 19h10"/></svg>
  </div></div>
  <div class="service__title">Business Consulting</div>
  <div class="service__text">Nemo enim ipsam voluptatem quia vo luptas sit aspernatur aut odit aut fugit sed quia conse quuntur</div>
  <div class="btn btn--grey">Read More</div>
</div>
<div class="abs service service--active" style="left:454px">
  <div class="service__icon"><div>
    <svg width="40" height="40" viewBox="0 0 40 40" fill="none" stroke="#fff" stroke-width="2.5"><rect x="5" y="7" width="30" height="21"/><path d="M20 28v5M13 34h14"/></svg>
  </div></div>
  <div class="service__title">Consumer Consulting</div>
  <div class="service__text">Nemo enim ipsam voluptatem quia vo luptas sit aspernatur aut odit aut fugit sed quia conse quuntur</div>
  <div class="btn btn--blue">Read More</div>
</div>
<div class="abs service" style="left:803px">
  <div class="service__icon"><div>
    <svg width="44" height="40" viewBox="0 0 44 40" fill="#fff"><circle cx="22" cy="12" r="6"/><circle cx="10" cy="15" r="4.5"/><circle cx="34" cy="15" r="4.5"/><path d="M12 32c0-8 4-12 10-12s10 4 10 12z"/><path d="M2 32c0-6 3-9 8-9 3 0 4 1 5 2-2 2-3 4-3 7z"/><path d="M42 32c0-6-3-9-8-9-3 0-4 1-5 2 2 2 3 4 3 7z"/></svg>
  </div></div>
  <div class="service__title">Financial Consulting</div>
  <div class="service__text">Nemo enim ipsam voluptatem quia vo luptas sit aspernatur aut odit aut fugit sed quia conse quuntur</div>
  <div class="btn btn--grey">Read More</div>
</div>

<!-- job search -->
<div class="abs search-band" role="img" aria-label="City skyline at dusk blended with a man in a dark suit"></div>
<svg class="abs search-band__tick" width="38" height="38" viewBox="0 0 38 38" fill="none" stroke="#f4c21c" stroke-width="3"><path d="M33 17a15 15 0 1 1-6-11"/><path d="M11 18l7 7 17-18"/></svg>
<div class="abs search-band__title"><span class="hl">Doing the right thing,</span><br><span class="wh">at the right time.</span></div>
<div class="abs search-input">Search jobs here..</div>
<div class="btn btn--blue" style="left:469px;top:1475px;width:106px;height:48px;font-size:16px">Search</div>

<!-- blogs -->
<h2 class="abs section-title" style="top:1622px">Our <span>Recent Blogs</span></h2>
<p class="abs section-lead" style="top:1670px">A unique destination for everything that practitioners need to execute best practice change management, transformation and project methodologies. The Learning Hub offering will be positioned as a place of learning.</p>

<div class="abs post" style="left:98px">
  <div class="post__image" role="img" aria-label="Photo of a group of business people in an office" style="background:linear-gradient(180deg,#dfe2e6,#6f6a6a 55%,#3a3838)"></div>
  <div class="post__title">Neque porro quisquam dolorem</div>
  <div class="post__text">Nemo enim ipsam voluptatem quia voluptas sit aspernatur aut odit aut fugit, sed quia conse quuntur magni dolores eosqui</div>
  <div class="btn btn--blue">Find Jobs</div>
</div>
<div class="abs post" style="left:451px">
  <div class="post__image" role="img" aria-label="Photo of a businesswoman working at a laptop" style="background:linear-gradient(180deg,#eef0f2,#b9bdc2 55%,#55575b)"></div>
  <div class="post__title">Neque porro quisquam dolorem</div>
  <div class="post__text">Nemo enim ipsam voluptatem quia voluptas sit aspernatur aut odit aut fugit, sed quia conse quuntur magni dolores eosqui</div>
  <div class="btn btn--grey">Find Jobs</div>
</div>
<div class="abs post" style="left:801px">
  <div class="post__image" role="img" aria-label="Photo of students studying with notebooks" style="background:linear-gradient(180deg,#e8e4dc,#a9859a 55%,#6e5b7a)"></div>
  <div class="post__title">Neque porro quisquam dolorem</div>
  <div class="post__text">Nemo enim ipsam voluptatem quia voluptas sit aspernatur aut odit aut fugit, sed quia conse quuntur magni dolores eosqui</div>
  <div class="btn btn--grey">Find Jobs</div>
</div>

<!-- footer -->
<footer class="abs footer"></footer>
<div class="abs footer__logo"><span>caldermoor</span><i></i></div>
<p class="abs footer__about">Nemo enim ipsam voluptatem quia voluptas sit aspernatur aut odit aut fugit, sed quia conse quuntur magni dolores</p>

<div class="abs footer__head" style="left:370px">QUICK LINKS</div>
<ul class="abs footer__links">
  <li>&gt;&gt;&nbsp; Home</li>
  <li>&gt;&gt;&nbsp; Find a Job</li>
  <li>&gt;&gt;&nbsp; Find Talent</li>
  <li>&gt;&gt;&nbsp; Our Services</li>
  <li>&gt;&gt;&nbsp; About us</li>
  <li>&gt;&gt;&nbsp; Contact us</li>
</ul>

<div class="abs footer__head" style="left:554px">CONTACT US</div>
<ul class="abs footer__contact">
  <li><svg width="10" height="14" viewBox="0 0 10 14" fill="#ddd"><path d="M5 0a5 5 0 0 1 5 5c0 4-5 9-5 9S0 9 0 5a5 5 0 0 1 5-5zm0 3a2 2 0 1 0 0 4 2 2 0 0 0 0-4z"/></svg><span>12 Orchard Row, Kestwick,<br>London</span></li>
  <li><svg width="12" height="10" viewBox="0 0 12 10" fill="#ddd"><path d="M0 0h12v10H0zM1 1l5 4 5-4"/></svg><span>Email: hello@caldermoor.example</span></li>
  <li><svg width="11" height="11" viewBox="0 0 11 11" fill="#ddd"><path d="M2 0l2 3-1 1c1 2 2 3 4 4l1-1 3 2-1 2C5 11 0 6 0 2z"/></svg><span>Phone: +1500 0000 00</span></li>
</ul>

<div class="abs footer__head" style="left:847px">NEWSLETTER</div>
<p class="abs footer__news">Lorem ipsum dolor sit amet, consectetur adipiscing elit dignissimos.</p>
<div class="abs news-input">Email</div>
<div class="btn btn--blue news-btn">SIGN UP NOW</div>

<div class="abs bottombar"></div>
<div class="abs bottombar__copy">© 2016 caldermoor. All Rights Reserved</div>
<span class="abs bottombar__social" style="left:918px"></span>
<span class="abs bottombar__social" style="left:968px"></span>
<span class="abs bottombar__social" style="left:1019px"></span>
<span class="abs bottombar__social" style="left:1069px"></span>

</body>
</html>
```